Computer Repair Business - Needs New Business Card Design

I want to create a very cool business card for my business. I want to make it 100% different from my previous card. I would like to use similar color scheme like Royal blue.

With this card I want to create a conversation and have my customers say "Wow, that's a cool business card" Trying to prevent it from looking like the typical card that get's shoved into a wallet.

My website is below:

www.lornapcfix.com

I want to edit the hours and website and email:

www.lornapcfix.com
lorna@lornapcfix.com

10:30 to 6pm Monday - Friday
10:30 to 3pm Saturday
Updates

Just to remind, when i see a new design i don't want to notice my old design.

Business card will be printed and made with rounded corners and horizontal.

The back of the card should say " In-Store Repair, Remote Support, Data Recovery"

Industry/Entity Type

Business

Font styles to use
Sans Serif

Colors
33a6d7
3176b5

Requirements
Must have
• Clean looking - have creative aspects.
Should not have
• Should not look like the previous card design.

```html
<!DOCTYPE html>
<html lang="en">
<head>
<meta charset="utf-8">
<title>Lorna PC Fix – Business Card</title>
<link rel="stylesheet" href="https://fonts.googleapis.com/css2?family=Montserrat:wght@500&family=Open+Sans:wght@400;600&family=Arimo:wght@400&display=swap">
<style>
  :root {
    --page-bg: #d8d3cb;
    --card-top: #f3f2ef;
    --card-bottom: #e6e4df;
    --ink: #2b2a2c;
    --ink-soft: #3d3c3f;
    --ink-muted: #5a595c;
    --royal: #1d5fb0;
    --royal-title: #2f6fb5;
    --sky: #33a6d7;
    --band-dark: #1f1c1e;
    --rule: #a9a8a8;
    --white: #ffffff;
  }
  * { margin: 0; padding: 0; box-sizing: border-box; }
  html, body {
    width: 1200px; height: 768px; overflow: hidden;
    background: var(--page-bg);
  }
  .card {
    position: absolute; left: 60px; top: 69px;
    width: 1080px; height: 630px;
    border-radius: 28px; overflow: hidden;
    background: linear-gradient(180deg, var(--card-top), var(--card-bottom));
    box-shadow: 0 10px 30px rgba(0,0,0,0.18);
    font-family: "Open Sans", Arial, sans-serif;
    color: var(--ink);
  }
  .holder-name {
    position: absolute; left: 46px; top: 200px;
    font-family: "Montserrat", Arial, sans-serif; font-weight: 500;
    font-size: 29px; letter-spacing: 1.5px; color: var(--ink);
  }
  .holder-title {
    position: absolute; left: 46px; top: 252px;
    font-weight: 600; font-size: 23px; letter-spacing: 0.5px; color: var(--royal-title);
  }
  .brand {
    position: absolute; right: 52px; top: 208px;
    display: flex; align-items: center; gap: 18px;
  }
  .brand-name {
    font-weight: 600; font-size: 56px; letter-spacing: 1px; color: var(--ink);
    line-height: 1;
  }
  .brand-mark {
    width: 42px; height: 42px; background: var(--royal);
  }
  .divider {
    position: absolute; left: 66px; top: 309px; width: 940px; height: 3px;
    background: linear-gradient(90deg, rgba(169,168,168,0), var(--rule) 20%, var(--rule) 80%, rgba(169,168,168,0));
  }
  .address {
    position: absolute; left: 46px; top: 396px;
    font-style: normal;
    font-size: 29px; line-height: 42px; color: var(--ink-soft);
  }
  .hours {
    position: absolute; left: 46px; top: 492px;
    list-style: none;
    font-size: 18px; line-height: 26px; color: var(--ink-muted);
  }
  .hours strong { font-weight: 600; color: var(--royal-title); }
  .contacts {
    position: absolute; right: 82px; top: 378px;
    list-style: none; text-align: right;
  }
  .contacts li {
    display: flex; justify-content: flex-end; align-items: center; gap: 14px;
    font-size: 22px; height: 46px; color: var(--ink-soft);
  }
  .contacts svg { width: 26px; height: 26px; fill: var(--royal); }
  .footer-band {
    position: absolute; left: 0; bottom: 0; width: 1080px; height: 52px;
  }
  .footer-url {
    position: absolute; left: 42px; bottom: 11px;
    font-family: "Arimo", Arial, sans-serif; font-size: 24px; color: var(--white);
  }
  .services {
    position: absolute; right: 44px; bottom: 14px;
    font-size: 18px; letter-spacing: 0.5px; color: var(--white);
  }
  .services .dot { color: var(--sky); margin: 0 8px; }
</style>
</head>
<body>
  <div class="card">
    <div class="holder-name">MARK ELLISON</div>
    <div class="holder-title">Managing Director</div>

    <div class="brand">
      <span class="brand-name">LORNA PC FIX</span>
      <span class="brand-mark"></span>
    </div>

    <div class="divider"></div>

    <address class="address">
      217 Maple Ave,<br>Fairview, NJ 07022
    </address>

    <ul class="hours">
      <li><strong>Mon – Fri</strong> 10:30 to 6pm</li>
      <li><strong>Saturday</strong> 10:30 to 3pm</li>
    </ul>

    <ul class="contacts">
      <li>555.014.2287
        <svg viewBox="0 0 24 24"><path d="M6.6 10.8c1.4 2.8 3.8 5.1 6.6 6.6l2.2-2.2c.3-.3.7-.4 1-.2 1.1.4 2.3.6 3.6.6.6 0 1 .4 1 1V20c0 .6-.4 1-1 1C10.6 21 3 13.4 3 4c0-.6.4-1 1-1h3.5c.6 0 1 .4 1 1 0 1.3.2 2.5.6 3.6.1.3 0 .7-.2 1z"/></svg>
      </li>
      <li>lorna@lornapcfix.com
        <svg viewBox="0 0 24 24"><path d="M2 5h20v14H2z M3.5 6.5v.4l8.5 6 8.5-6v-.4z" fill-rule="evenodd"/></svg>
      </li>
      <li>www.lornapcfix.com
        <svg viewBox="0 0 24 24"><path d="M12 2a10 10 0 1 0 0 20 10 10 0 0 0 0-20zm6.9 6h-3a15 15 0 0 0-1.3-3.9A8 8 0 0 1 18.9 8zM12 4c.8 1.1 1.5 2.5 1.9 4h-3.8c.4-1.5 1.1-2.9 1.9-4zM4.3 14a8 8 0 0 1 0-4h3.4a16 16 0 0 0 0 4zm.8 2h3a15 15 0 0 0 1.3 3.9A8 8 0 0 1 5.1 16zm3-8h-3a8 8 0 0 1 4.3-3.9A15 15 0 0 0 8.1 8zM12 20c-.8-1.1-1.5-2.5-1.9-4h3.8c-.4 1.5-1.1 2.9-1.9 4zm2.3-6H9.7a14 14 0 0 1 0-4h4.6a14 14 0 0 1 0 4zm.3 5.9a15 15 0 0 0 1.3-3.9h3a8 8 0 0 1-4.3 3.9zM16.3 14a16 16 0 0 0 0-4h3.4a8 8 0 0 1 0 4z"/></svg>
      </li>
    </ul>

    <svg class="footer-band" viewBox="0 0 1080 52" preserveAspectRatio="none">
      <rect x="0" y="2" width="1080" height="50" fill="var(--band-dark)"/>
      <path d="M0 0 H405 C430 0 440 10 452 30 L465 52 H0 Z" fill="#9a9a9a"/>
      <path d="M0 0 H398 C422 0 432 10 444 30 L457 52 H0 Z" fill="var(--royal)"/>
    </svg>
    <div class="footer-url">www.lornapcfix.com</div>
    <div class="services">In-Store Repair<span class="dot">•</span>Remote Support<span class="dot">•</span>Data Recovery</div>
  </div>
</body>
</html>
```